Stationary design for boutique production house

We need a stationary design for our production house, 'Lorno Productions' based in Singapore. We produce microfilms as well as podcasts, talkshows and events. Our logo is a stylized icon of our director, who is also the executive producer and host of our programs, Lorno. Our main company colors are Red, Black and white. We would like a clean, minimalist design incorporating our existing company logo that conveys a sense of urbanism and elegance.

Logo and font files are attached. f

Target Market(s)

We focus on lifestyle media rather than entertainment.

Industry/Entity Type

Boutique

Font styles to use
Serif
Sans Serif

Colors
ec1f27
ffffff
000000

Requirements
Must have
• Our company logo and at least one of our company colors.
Nice to have
• Our address and contact information.
Should not have
• Changes made to the company logo (using only certain parts of it is fine though)

```html
<!DOCTYPE html>
<html lang="en">
<head>
<meta charset="utf-8">
<title>Lorno Productions — Stationery</title>
<link href="https://fonts.googleapis.com/css2?family=Libre+Baskerville:ital,wght@0,400;0,700;1,400&family=Open+Sans:wght@400;600&display=swap" rel="stylesheet">
<style>
  :root {
    --red: #ec1f27;
    --black: #1b1b1b;
    --ink: #000000;
    --white: #ffffff;
    --paper-grey: #e4e4e4;
    --emboss: #0f0f0f;
    --body-text: #444444;
    --serif: "Libre Baskerville", Georgia, serif;
    --sans: "Open Sans", Arial, sans-serif;
  }
  * { box-sizing: border-box; margin: 0; padding: 0; }
  html, body { width: 1200px; height: 900px; overflow: hidden; }
  body { background: var(--paper-grey); position: relative; font-family: var(--sans); }

  /* Wordmark: single line, one colour, one weight, one small square beside it */
  .wordmark { display: inline-flex; align-items: center; gap: 8px; font-family: var(--serif); font-weight: 400; line-height: 1; white-space: nowrap; color: inherit; }
  .wordmark .square { width: .5em; height: .5em; background: currentColor; flex: none; }

  /* Notebook cover */
  .notebook { position: absolute; left: 60px; top: 40px; width: 320px; height: 420px; background: var(--black); border-radius: 4px 10px 10px 4px; }
  .notebook .band { position: absolute; right: 44px; top: 0; width: 8px; height: 100%; background: var(--ink); }
  .notebook .mark-area { position: absolute; left: 0; right: 52px; top: 196px; display: flex; justify-content: center; color: var(--emboss); font-size: 22px; }

  /* Business cards */
  .card { position: absolute; top: 520px; width: 190px; height: 280px; border-bottom: 5px solid var(--red); display: flex; flex-direction: column; align-items: center; }
  .card--front-dark { left: 60px; background: var(--black); color: var(--white); justify-content: center; }
  .card--front-light { left: 280px; background: var(--white); color: var(--ink); justify-content: center; }
  .card--back { left: 500px; background: var(--black); color: var(--white); padding-top: 44px; }
  .card .wordmark { font-size: 15px; }
  .card--back .wordmark { font-size: 13px; }
  .card-person { margin-top: 34px; text-align: center; font-family: var(--serif); }
  .card-person .name { font-size: 12px; letter-spacing: .08em; }
  .card-person .role { font-size: 10px; font-style: italic; color: var(--red); margin-top: 3px; }
  .card-contact { margin-top: 16px; font-family: var(--serif); font-size: 9px; line-height: 1.6; text-align: center; }
  .card-contact .web { color: var(--red); }

  /* Letterhead */
  .letterhead { position: absolute; left: 700px; top: 40px; width: 460px; height: 650px; background: var(--white); display: flex; flex-direction: column; }
  .letterhead-top { height: 70px; background: var(--black); border-bottom: 2px solid var(--red); }
  .letterhead .mark-area { margin-top: 28px; display: flex; justify-content: center; font-size: 15px; color: var(--ink); }
  .letter { padding: 34px 40px 0; color: var(--body-text); font-size: 9px; line-height: 1.6; flex: 1; }
  .letter-sender { font-size: 11px; }
  .letter-date { font-size: 9px; margin-bottom: 14px; }
  .letter p { margin-bottom: 12px; }
  .signature { width: 110px; height: 26px; margin: 14px 0 0 auto; background: linear-gradient(90deg, #dcdcdc, #f2f2f2); border-radius: 13px; }
  .letterhead-foot { height: 80px; background: var(--black); border-top: 2px solid var(--red); color: var(--white); font-family: var(--serif); font-size: 9px; text-align: center; display: flex; flex-direction: column; justify-content: center; gap: 4px; }
  .letterhead-foot .pin { width: 12px; height: 12px; margin: 0 auto; }
  .letterhead-foot .web { color: var(--red); }
</style>
</head>
<body>

<section class="notebook" aria-label="Notebook cover">
  <div class="mark-area"><span class="wordmark"><span class="square"></span>Lorno Productions</span></div>
  <div class="band"></div>
</section>

<section class="card card--front-dark" aria-label="Business card front, dark">
  <span class="wordmark"><span class="square"></span>Lorno Productions</span>
</section>

<section class="card card--front-light" aria-label="Business card front, light">
  <span class="wordmark"><span class="square"></span>Lorno Productions</span>
</section>

<section class="card card--back" aria-label="Business card back">
  <span class="wordmark"><span class="square"></span>Lorno Productions</span>
  <div class="card-person">
    <div class="name">LORNO HALE</div>
    <div class="role">Director</div>
  </div>
  <div class="card-contact">
    Street Address Line 1<br>
    Your City, Postal Code<br>
    T: +00 (0)00 0000<br>
    F: +00 (0)00 0000<br>
    E: info@lornoproductions.com<br>
    <span class="web">www.lornoproductions.com</span>
  </div>
</section>

<section class="letterhead" aria-label="Letterhead">
  <div class="letterhead-top"></div>
  <div class="mark-area"><span class="wordmark"><span class="square"></span>Lorno Productions</span></div>
  <div class="letter">
    <div class="letter-sender">Lorno Productions</div>
    <div class="letter-date">December 22, 2014/Revised February 2, 2015</div>
    <p>We shape stories for the city, from short films and podcasts to live talks and curated events. Each project is built with care, clear purpose and a calm, elegant hand.</p>
    <p>Our studio works closely with brands and hosts to plan, film and edit content that feels true to urban life. We keep teams small, timelines honest and every detail in view, from the first idea to the final cut and release.</p>
    <p>Thank you for your time and interest. We look forward to working together on the next season of programs and sharing more news soon.</p>
    <div class="signature" role="img" aria-label="Handwritten signature"></div>
  </div>
  <footer class="letterhead-foot">
    <svg class="pin" viewBox="0 0 12 12" aria-hidden="true"><circle cx="6" cy="6" r="6" fill="#ec1f27"/><circle cx="6" cy="5" r="2" fill="#1b1b1b"/></svg>
    <div>Street Address Line 1, Your City, Postal Code</div>
    <div>T: +00 (0)00 0000 | F: +00 (0)00 0000 | E: info@lornoproductions.com</div>
    <div class="web">www.lornoproductions.com</div>
  </footer>
</section>

</body>
</html>
```